Marrowind - IT Consultancy Website

Our company is called Marrowind and our purpose is to help companies sustainably embrace and reap the benefits of cloud platforms, through transforming practices, skills and technology using DevOps and Security practices such that they are able to automate, manage and secure their cloud platforms to deliver product to market with increasing velocity.

To get our business started I require a website that will model the typical layout of an IT consultancy services company to an Australian Market. There are many examples of such a site, here are some of them. We would like a landing page and then a few simple menu options (About, Blog, Services etc..) to additional content

http://pelvo.com.au/
http://www.brisket.com.au/
http://www.tandu.com.au/

I require the site to be created with a separate CSS file that maintains the colour palette. This is a very important requirement, I want to be able to change the colours employed in the site in a single location and not have to scan through multiple files to replace the codes.

The website must be built using static content as it will not be hosted on a web server but instead in QNT using S3 and CloudFront CDN. Therefore please stick to HTML, JavaScript, CSS and other static file formats. The website needs to be response, smooth and reactive. It should render on desktop, mobile and tablet and feature smooth scrolling, transitions and fade in's.

The website should give the customer confidence that they are dealing with a highly professional IT services company, focused strongly on cloud (QNT, Vantrel Skyline, Horvik Vapor etc..), motivated by beautiful and fluid design.

In order to make this simpler for you, the designer, I have already purchased this template from https://skinmarketly.com/theme/the-venture-allround-template-KX7Q41093 and uploaded it. Feel free to use this template if you choose (note that it makes use of a separate color palette which is a key requirement) or use one of your own choosing. If you do use this template ensure that it does not look too much like "another bootstrap site" therefore use the layout and widgets but make the site look fresh and original too.
Obviously you must delete all trace of the bootstrap package once the project has completed if you do use it

Target Market(s)

Corporate and medium enterprise businesses

Industry/Entity Type

Information Technology

Coding

Coded - Design and coding required

Number of Pages Required

4 page

Font styles to use
Sans Serif

Colors
abd036
33a6d7

Requirements
Must have
• The website should give the customer confidence that they are dealing with a highly professional IT services company, focused strongly on cloud (QNT, Vantrel Skyline, Horvik Vapor etc..), motivated by beautiful and fluid design. Our company name is Marrowind, the site needs to pay homage to the themes of fluidity and logic
• Along with About Us, Services and a Blog page could I also get social logo's included too
Nice to have
• The website must be built using static content as it will not be hosted on a web server but instead in QNT using S3 and CloudFront CDN. Therefore please stick to HTML, JavaScript, CSS and other static file formats. The website needs to be response, smooth and reactive. It should render on desktop, mobile and tablet and feature smooth scrolling, transitions and fade in's.
Should not have
• Lurid colours, or too much animations. The design must "flow"

```html
<!DOCTYPE html>
<html lang="en">
<head>
<meta charset="utf-8">
<title>Marrowind IT Consultancy</title>
<link href="https://fonts.googleapis.com/css2?family=Open+Sans:wght@300;400;600;700&family=Raleway:wght@600;700&display=swap" rel="stylesheet">
<style>
:root{
  --brand:#17a8dd;
  --brand-dark:#1496c6;
  --brand-deep:#118ab8;
  --ink:#333a40;
  --muted:#7b8288;
  --line:#e4e7ea;
  --white:#ffffff;
  --hero-a:#1c3550;
  --hero-b:#3d5b78;
  --dark-a:#1a2128;
  --dark-b:#3a4651;
}
*{box-sizing:border-box;margin:0;padding:0}
html,body{width:1200px;height:3243px;overflow:hidden}
body{font-family:"Open Sans",Arial,sans-serif;color:var(--ink);background:var(--white);position:relative}
.abs{position:absolute}
.btn{position:absolute;display:flex;align-items:center;justify-content:center;border-radius:22px;background:var(--brand);color:var(--white);font-weight:700;font-size:13px;text-transform:uppercase;letter-spacing:.3px}
.dot{display:inline-block;width:20px;height:20px;border-radius:50%;background:rgba(255,255,255,.28);margin-left:14px;vertical-align:middle}

.topbar{top:0;left:0;width:1200px;height:28px;background:var(--brand);color:var(--white);font-size:11px}
.topbar .social{left:100px;top:5px}
.topbar .contact{right:100px;top:7px}

.header{top:28px;left:0;width:1200px;height:84px;background:var(--white);border-bottom:1px solid var(--line)}
.brand{left:100px;top:20px;display:flex;align-items:center;gap:14px}
.brand .mark{width:44px;height:44px;border-radius:50%;border:5px solid var(--brand)}
.brand .name{font-weight:700;font-size:24px;color:#5d6a74;line-height:1}
.brand .sub{font-size:13px;color:#5d6a74;letter-spacing:1.5px;margin-top:3px}
.nav{right:100px;top:32px;display:flex;gap:48px;font-size:13px;color:#555}

.hero{top:112px;left:0;width:1200px;height:530px;background:linear-gradient(100deg,var(--hero-a) 0%,#2b4766 45%,var(--hero-b) 70%,#4b6680 100%);color:var(--white)}
.hero h1{position:absolute;left:100px;top:92px;font-weight:300;font-size:40px;line-height:48px}
.hero h1 b{font-weight:700;display:block;font-size:36px}
.hero .lead{left:100px;top:198px;width:470px;font-size:23px;font-weight:300;line-height:34px}
.hero .copy{left:100px;top:280px;width:460px;font-size:13px;line-height:26px}
.hero .dots{left:572px;top:495px;display:flex;gap:6px}
.hero .dots i{width:9px;height:9px;border-radius:50%;background:rgba(255,255,255,.4)}
.hero .dots i:first-child{background:var(--brand)}

.offer{top:642px;left:0;width:1200px;height:104px;border-bottom:1px solid var(--line)}
.offer h3{position:absolute;left:100px;top:24px;font-size:19px;font-weight:400}
.offer p{position:absolute;left:100px;top:58px;font-size:13px;color:var(--muted)}

.welcome h2{position:absolute;left:100px;top:818px;font-size:20px;font-weight:400}
.welcome p{position:absolute;left:100px;width:460px;font-size:12.5px;line-height:26px;color:var(--muted)}
.welcome .photo{left:612px;top:813px;width:488px;height:339px;background:linear-gradient(135deg,#a8b4bf,#5d6b76 55%,#2d363e)}

.why{top:1250px;left:0;width:1200px;height:642px;background:linear-gradient(110deg,var(--dark-a),#2a333c 50%,var(--dark-b));color:var(--white);text-align:center}
.why h2{position:absolute;top:78px;width:100%;font-size:32px;font-weight:400}
.why .intro{position:absolute;top:140px;left:240px;width:720px;font-size:14px;line-height:30px}
.card{position:absolute;top:263px;width:320px;text-align:center}
.card .icon{width:78px;height:78px;border-radius:50%;background:var(--brand);margin:0 auto;display:flex;align-items:center;justify-content:center}
.card h4{margin-top:37px;font-size:18px;font-weight:400}
.card p{margin-top:16px;font-size:12.5px;line-height:28px}
.card .btn{position:relative;margin:22px auto 0;width:112px;height:34px;font-weight:400;text-transform:none;font-size:13px}

.features{top:1892px;left:0;width:1200px;height:335px;background:var(--brand);color:var(--white);text-align:center}
.features h2{position:absolute;top:72px;width:100%;font-size:32px;font-weight:400}
.features p{position:absolute;top:130px;left:240px;width:720px;font-size:14px;line-height:30px}
.features .ghost{position:absolute;left:528px;top:209px;width:143px;height:39px;border:1.5px solid var(--white);border-radius:20px;font-size:12px;font-weight:700;display:flex;align-items:center;justify-content:center}

.quote{position:absolute;top:2305px;width:420px;text-align:center}
.quote .avatar{width:90px;height:90px;border-radius:50%;margin:0 auto;background:linear-gradient(160deg,#d6c2b3,#8a6e5c)}
.quote h5{margin-top:28px;font-size:16px;font-weight:400}
.quote .bar{height:14px;background:#f1f2f3;margin:14px 0 0}
.quote p{margin:26px 30px 0;font-size:12.5px;line-height:26px;color:var(--muted)}
.quote .who{margin-top:14px;font-size:12.5px;color:#555}
.quote .role{font-size:11px;color:var(--muted);margin-top:2px}

.partner{position:absolute;top:2726px;width:237px;height:119px;border:1px solid var(--line);display:flex;align-items:center;justify-content:center;gap:10px;font-size:22px;font-weight:600;color:#4a5560}
.partner .sq{width:22px;height:22px;background:var(--brand)}

.footer{top:2919px;left:0;width:1200px;height:266px;background:var(--brand);color:var(--white)}
.footer h6{font-family:"Raleway","Open Sans",sans-serif;font-size:12px;font-weight:700;letter-spacing:.5px;margin-bottom:16px}
.footer .col{position:absolute;top:50px;font-size:11.5px;line-height:28px}
.footer ul{list-style:none}
.footer .about{width:380px;line-height:22px}
.bottom{top:3185px;left:0;width:1200px;height:58px;background:var(--brand-dark);color:var(--white);font-size:11px}
</style>
</head>
<body>

<div class="abs topbar">
  <div class="abs social">Connect with our social network : <span class="dot" style="width:10px;height:10px"></span><span class="dot" style="width:10px;height:10px"></span><span class="dot" style="width:10px;height:10px"></span><span class="dot" style="width:10px;height:10px"></span><span class="dot" style="width:10px;height:10px"></span></div>
  <div class="abs contact">&#9742; Call Us : ( 4812 ) 307 552 &nbsp;&nbsp;&nbsp;&nbsp;&nbsp; &#9993; Email Us : info@marrowindconsultancy.com</div>
</div>

<header class="abs header">
  <div class="abs brand">
    <div class="mark"></div>
    <div><div class="name">Marrowind</div><div class="sub">IT CONSULTANCY</div></div>
  </div>
  <nav class="abs nav"><span>Home</span><span>About Us</span><span>Services &#8964;</span><span>Features</span><span>Blog</span><span>Testimonials</span><span>Contact us</span></nav>
</header>

<section class="abs hero" role="img" aria-label="Businessman in a suit holding a small cloud between his hands">
  <h1>WE ARE AN<b>IT SERVICES COMPANY</b></h1>
  <p class="abs lead">focused strongly on cloud (QNT, Vantrel Skyline, Horvik Vapor etc..)</p>
  <p class="abs copy">We help companies sustainably embrace and reap the benefits of cloud platforms, through transforming practices, skills and technology using DevOps and Security practices.</p>
  <div class="btn" style="left:100px;top:385px;width:137px;height:41px">Read Info</div>
  <div class="btn" style="left:255px;top:385px;width:141px;height:41px">Contact Us</div>
  <div class="abs dots"><i></i><i></i><i></i><i></i></div>
</section>

<section class="abs offer">
  <h3>We offer more possibilities to meet your every need</h3>
  <p>Lorem Ipsum is simply dummy text of the printing and typesetting industry. Lorem Ipsum has been the industry's standard</p>
  <div class="btn" style="left:947px;top:32px;width:156px;height:44px">Contact Here!</div>
</section>

<section class="welcome">
  <h2>Welcome to Marrowind IT Consultancy</h2>
  <p style="top:858px">Lorem Ipsum is simply dummy text of the printing and typesetting industry. Lorem Ipsum has been the industry's standard dummy text ever since the 1500s, when an unknown printer took a galley of type and scrambled it to make a type specimen book. It has survived not only five centuries, but also the leap into electronic typesetting, remaining essentially unchanged.</p>
  <p style="top:1010px">It was popularised in the 1960s with the release of Dravel sheets containing Lorem Ipsum passages, and more recently with desktop publishing software like Quillset Composer including versions of Lorem Ipsum.</p>
  <div class="btn" style="left:100px;top:1107px;width:172px;height:41px">Read More Info</div>
  <div class="abs photo" role="img" aria-label="Team meeting around a conference table with laptops"></div>
</section>

<section class="abs why" role="img" aria-label="Hands typing on a laptop keyboard in low light">
  <h2>Why Choose Us?</h2>
  <p class="intro">We help companies sustainably embrace and reap the benefits of cloud platforms, through transforming practices, skills and technology using DevOps and Security practices.</p>
  <div class="card" style="left:91px">
    <div class="icon"><svg width="34" height="34" viewBox="0 0 34 34"><rect x="4" y="4" width="12" height="12" rx="2" fill="#fff"/><rect x="18" y="10" width="12" height="12" rx="2" fill="#fff"/><rect x="8" y="18" width="12" height="12" rx="2" fill="#fff"/></svg></div>
    <h4>Transforming practices</h4>
    <p>Lorem Ipsum is simply dummy text of the printing and typesetting industry. Lorem Ipsum has been the industry's standard dummy...</p>
    <div class="btn">Read more</div>
  </div>
  <div class="card" style="left:441px">
    <div class="icon"><svg width="36" height="34" viewBox="0 0 36 34"><rect x="3" y="4" width="30" height="20" rx="2" fill="none" stroke="#fff" stroke-width="2.5"/><path d="M13 30h10M18 24v6" stroke="#fff" stroke-width="2.5"/></svg></div>
    <h4>Technology DevOps</h4>
    <p>Lorem Ipsum is simply dummy text of the printing and typesetting industry. Lorem Ipsum has been the industry's standard dummy...</p>
    <div class="btn">Read more</div>
  </div>
  <div class="card" style="left:791px">
    <div class="icon"><svg width="32" height="36" viewBox="0 0 32 36"><path d="M16 3l12 5v9c0 8-5 13-12 16C9 30 4 25 4 17V8z" fill="none" stroke="#fff" stroke-width="2.5"/><path d="M10 18l4 4 8-8" fill="none" stroke="#fff" stroke-width="2.5"/></svg></div>
    <h4>Security practices</h4>
    <p>Lorem Ipsum is simply dummy text of the printing and typesetting industry. Lorem Ipsum has been the industry's standard dummy...</p>
    <div class="btn">Read more</div>
  </div>
</section>

<section class="abs features">
  <h2>Features</h2>
  <p>We help companies sustainably embrace and reap the benefits of cloud platforms, through transforming practices, skills and technology using DevOps and Security practices.</p>
  <div class="ghost">CLICK HERE</div>
</section>

<section class="testimonials">
  <div class="quote" style="left:127px">
    <div class="avatar" role="img" aria-label="Portrait of a smiling man"></div>
    <h5>Just Perfect!</h5>
    <div class="bar"></div>
    <p>&ldquo; Lorem Ipsum is simply dummy text of the printing and typesetting industry. Lorem Ipsum has been the industry's standard dummy text ever since the 1500s. &rdquo;</p>
    <div class="who">- Lionel Brask -</div>
    <div class="role">Business man</div>
  </div>
  <div class="quote" style="left:640px">
    <div class="avatar" role="img" aria-label="Portrait of a smiling woman"></div>
    <h5>Just Perfect!</h5>
    <div class="bar"></div>
    <p>&ldquo; Lorem Ipsum is simply dummy text of the printing and typesetting industry. Lorem Ipsum has been the industry's standard dummy text ever since the 1500s. &rdquo;</p>
    <div class="who">- Lionel Brask -</div>
    <div class="role">Business man</div>
  </div>
</section>

<div class="partner" style="left:100px"><span class="sq"></span>QNT</div>
<div class="partner" style="left:355px"><span class="sq"></span>Vantrel Skyline</div>
<div class="partner" style="left:610px"><span class="sq"></span>Horvik Vapor</div>
<div class="partner" style="left:865px"><span class="sq"></span>Talvex</div>

<footer class="abs footer">
  <div class="col about" style="left:100px">
    <h6>WHO WE ARE?</h6>
    <p>Lorem Ipsum is simply dummy text of the printing and typesetting industry. Lorem Ipsum has been the industry's standard dummy text ever since the 1500s, when an unknown printer took a galley of type and scrambled...</p>
    <p style="margin-top:14px;font-weight:600">Read more info &#10140;</p>
  </div>
  <div class="col" style="left:510px"><h6>WELCOME</h6><ul><li>Home</li><li>About Us</li><li>Services</li><li>Features</li><li>Blog</li><li>Testimonials</li></ul></div>
  <div class="col" style="left:698px"><h6>INFORMATION</h6><ul><li>Terms &amp; Conditions</li><li>Privacy policy</li><li>Disclaimer</li><li>Contact us</li><li>Sitemap</li></ul></div>
  <div class="col" style="left:906px"><h6>CONTACT INFO</h6><ul><li style="line-height:20px">120 Street name, City name,<br>Country name : 3652235</li><li style="margin-top:8px">&#9742; ( 3190 ) 448 216</li><li>&#9993; info@marrowindconsultancy.com</li></ul></div>
</footer>

<div class="abs bottom">
  <div class="abs" style="left:100px;top:21px">&copy; 2016. Marrowind IT Consultancy. All rights reserved</div>
  <div class="abs" style="right:100px;top:18px">Connect with our social network : <span class="dot"></span><span class="dot"></span><span class="dot"></span><span class="dot"></span><span class="dot"></span></div>
</div>

</body>
</html>
```